Morlavik APP redesign and color change

I am looking for a new design for my app. Please see the attached current design.

Currently, I have a functioning app but the colors and design are awful!
The logo is great but the rest of the app needs a refresh.
(Logo hi res not yet available but will upload soon.)
New colors or anything that is cutting edge.

Basically: It is a secure social media app within a school system where the teachers, students and parents can text, exchange photos, plan curriculum, etc.

I NEED ONLY landing page with a new look!
Looking for one distinct design for the landing page with new look.
The developer will apply this one design towards the rest of the pages/app screens.

Because part of the social media I need the feel and look of what is now the trend. Something that will attract and keep the client(s) interested. I am really leaving all the creative work to the designer and open to any suggestions.

Target Market(s)

Schools, community, teachers, students, colleges, sport teams

Industry/Entity Type

Non Profit

Font styles to use
Serif
Sans Serif

Colors

Designer to choose colors to be used in the design.

Requirements
Must have
• Sharp, trendy, millennial feel
Nice to have
• Up to designer
Should not have
• Up to designer

```html
<!DOCTYPE html>
<html lang="en">
<head>
<meta charset="utf-8">
<title>Morlavik — Landing Screen Concepts</title>
<link href="https://fonts.googleapis.com/css2?family=Montserrat:wght@600;800&family=Varela+Round&display=swap" rel="stylesheet">
<style>
  :root {
    --board: #222831;
    --white: #ffffff;
    --violet-start: #4f44c2;
    --violet-end: #6c86f1;
    --teal-start: #3fbcbd;
    --teal-end: #5ccfd0;
    --teal-deep: #2aa9ad;
    --button-text: #3cc0c4;
  }
  * { box-sizing: border-box; margin: 0; padding: 0; }
  html, body { width: 1024px; height: 1200px; overflow: hidden; background: var(--board); }
  .board {
    position: absolute; left: 0; top: 0;
    width: 1280px; height: 1500px;
    transform: scale(0.8); transform-origin: 0 0;
  }
  .concept-label {
    position: absolute; width: 334px; text-align: center;
    font-family: "Montserrat", sans-serif; font-weight: 800; font-size: 40px;
    color: var(--white); transform: translateY(-50%);
  }
  .screen {
    position: absolute; width: 334px; height: 594px; overflow: hidden;
    font-family: "Varela Round", sans-serif; color: var(--white);
    box-shadow: 0 6px 18px rgba(0,0,0,.35);
  }
  .screen--violet { background: linear-gradient(160deg, var(--violet-start) 0%, #5a52d3 50%, var(--violet-end) 100%); }
  .screen--teal { background: var(--teal-start); }
  .screen-photo {
    position: absolute; inset: 0;
    background:
      radial-gradient(ellipse at 30% 70%, rgba(42,160,165,.6), transparent 60%),
      radial-gradient(ellipse at 80% 30%, rgba(110,214,214,.5), transparent 55%),
      linear-gradient(180deg, var(--teal-end), var(--teal-start) 60%, var(--teal-deep));
  }
  .status-bar {
    position: absolute; left: 0; top: 0; width: 100%; height: 16px;
    font-family: "Montserrat", sans-serif; font-weight: 600; font-size: 11px;
  }
  .status-bar .signal { position: absolute; left: 16px; top: 3px; }
  .status-bar .clock { position: absolute; left: 0; width: 100%; top: 1px; text-align: center; }
  .status-bar .battery { position: absolute; right: 14px; top: 1px; display: flex; align-items: center; gap: 4px; }
  .word-cloud { position: absolute; inset: 0; }
  .screen--muted .word-cloud { opacity: .55; }
  .word {
    position: absolute; white-space: nowrap; transform: translateY(-50%);
    font-size: 15px; opacity: .3;
  }
  .word--md { font-size: 20px; opacity: .55; }
  .word--lg { font-size: 26px; opacity: .55; }
  .word--bright { opacity: .85; }
  .word--faint { opacity: .2; }
  .brand {
    position: absolute; left: 0; width: 100%; text-align: center;
  }
  .brand-mark {
    position: absolute; left: 50%; transform: translateX(-50%);
    border: 4px solid var(--white); border-radius: 50%;
  }
  .brand-name {
    position: absolute; left: 0; width: 100%; text-align: center;
    font-family: "Montserrat", sans-serif; font-weight: 600;
    color: var(--white); transform: translateY(-50%);
  }
  .tagline {
    position: absolute; left: 0; width: 100%; top: 441px; text-align: center;
    font-family: "Montserrat", sans-serif; font-size: 13px; line-height: 17px;
  }
  .cta {
    position: absolute; left: 20px; top: 505px; width: 296px; height: 45px;
    background: var(--white); border-radius: 23px;
    display: flex; align-items: center; justify-content: center; gap: 14px;
    font-family: "Montserrat", sans-serif; font-weight: 600; font-size: 13px;
    letter-spacing: 4px; color: var(--button-text);
    box-shadow: 0 3px 8px rgba(0,0,0,.15);
  }
</style>
</head>
<body>
<main class="board">

  <!-- Concept 1 -->
  <h2 class="concept-label" style="left:282px; top:72px;">#1</h2>
  <section class="screen screen--violet" style="left:282px; top:120px;">
    <div class="status-bar">
      <svg class="signal" width="50" height="10" viewBox="0 0 50 10"><g fill="#fff"><circle cx="3" cy="5" r="2.5"/><circle cx="9" cy="5" r="2.5"/><circle cx="15" cy="5" r="2.5"/></g><g fill="none" stroke="#fff"><circle cx="21" cy="5" r="2"/><circle cx="27" cy="5" r="2"/></g><path d="M36 7 l3 3 3-3 M34 4.5 a7 7 0 0 1 10 0" fill="none" stroke="#fff" stroke-width="1.4"/></svg>
      <div class="clock">4:21 PM</div>
      <div class="battery">100% <svg width="24" height="10" viewBox="0 0 24 10"><rect x="0" y="0" width="22" height="10" rx="2" fill="#fff"/><rect x="22" y="3" width="2" height="4" fill="#fff"/></svg></div>
    </div>
    <div class="word-cloud">
      <span class="word word--md" style="left:21px;top:68px">guardian</span>
      <span class="word" style="left:169px;top:62px">activity</span>
      <span class="word" style="left:61px;top:105px">curriculum</span>
      <span class="word" style="left:263px;top:105px">learn</span>
      <span class="word word--md word--bright" style="left:147px;top:129px">guidance</span>
      <span class="word" style="left:26px;top:145px">learner</span>
      <span class="word" style="left:254px;top:156px">secure</span>
      <span class="word word--md" style="left:67px;top:174px">student</span>
      <span class="word word--lg word--bright" style="left:189px;top:185px">safe</span>
      <span class="word" style="left:143px;top:209px">parent</span>
      <span class="word" style="left:269px;top:209px">tutor</span>
      <span class="word" style="left:55px;top:226px">teacher</span>
      <span class="word" style="left:219px;top:235px">texting</span>
      <span class="word" style="left:11px;top:258px">community</span>
      <span class="word" style="left:252px;top:270px">teaching</span>
      <span class="word word--lg" style="left:20px;top:287px">chat</span>
      <span class="word" style="left:59px;top:312px">school</span>
      <span class="word word--md word--bright" style="left:215px;top:321px">education</span>
      <span class="word" style="left:17px;top:344px">educator</span>
      <span class="word word--faint" style="left:267px;top:369px">society</span>
      <span class="word word--md" style="left:111px;top:390px">text</span>
      <span class="word" style="left:26px;top:406px">guardian</span>
      <span class="word" style="left:174px;top:398px">activity</span>
      <span class="word word--md word--bright" style="left:244px;top:410px">platform</span>
      <span class="word" style="left:66px;top:442px">online</span>
      <span class="word word--faint" style="left:150px;top:438px">collaboration</span>
      <span class="word word--md" style="left:152px;top:466px">social</span>
      <span class="word word--faint" style="left:32px;top:482px">media</span>
      <span class="word word--faint" style="left:259px;top:493px">pupil</span>
      <span class="word word--md" style="left:90px;top:506px;font-size:16px">guiding</span>
      <span class="word word--md" style="left:175px;top:510px;opacity:.3">learning</span>
      <span class="word word--faint" style="left:35px;top:524px">guru</span>
      <span class="word word--faint" style="left:275px;top:546px">voice</span>
      <span class="word word--lg" style="left:22px;top:563px;opacity:.3">collaborative</span>
      <span class="word word--faint" style="left:224px;top:572px">friendly</span>
    </div>
    <div class="brand-mark" style="top:242px;width:80px;height:80px;"></div>
    <div class="brand-name" style="top:362px;font-size:17px;letter-spacing:9px;">MORLAVIK</div>
  </section>

  <!-- Concept 2 -->
  <h2 class="concept-label" style="left:667px; top:72px;">#2</h2>
  <section class="screen screen--violet screen--muted" style="left:667px; top:120px;">
    <div class="status-bar">
      <svg class="signal" width="50" height="10" viewBox="0 0 50 10"><g fill="#fff"><circle cx="3" cy="5" r="2.5"/><circle cx="9" cy="5" r="2.5"/><circle cx="15" cy="5" r="2.5"/></g><g fill="none" stroke="#fff"><circle cx="21" cy="5" r="2"/><circle cx="27" cy="5" r="2"/></g><path d="M36 7 l3 3 3-3 M34 4.5 a7 7 0 0 1 10 0" fill="none" stroke="#fff" stroke-width="1.4"/></svg>
      <div class="clock">4:21 PM</div>
      <div class="battery">100% <svg width="24" height="10" viewBox="0 0 24 10"><rect x="0" y="0" width="22" height="10" rx="2" fill="#fff"/><rect x="22" y="3" width="2" height="4" fill="#fff"/></svg></div>
    </div>
    <div class="word-cloud">
      <span class="word word--md" style="left:21px;top:68px">guardian</span>
      <span class="word" style="left:169px;top:62px">activity</span>
      <span class="word" style="left:61px;top:105px">curriculum</span>
      <span class="word" style="left:263px;top:105px">learn</span>
      <span class="word word--md" style="left:147px;top:129px">guidance</span>
      <span class="word" style="left:26px;top:145px">learner</span>
      <span class="word" style="left:254px;top:156px">secure</span>
      <span class="word word--md" style="left:67px;top:174px">student</span>
      <span class="word word--lg" style="left:189px;top:185px">safe</span>
      <span class="word" style="left:143px;top:209px">parent</span>
      <span class="word" style="left:269px;top:209px">tutor</span>
      <span class="word" style="left:55px;top:226px">teacher</span>
      <span class="word" style="left:219px;top:235px">texting</span>
      <span class="word" style="left:11px;top:258px">community</span>
      <span class="word" style="left:252px;top:270px">teaching</span>
      <span class="word word--lg" style="left:20px;top:287px">chat</span>
      <span class="word" style="left:59px;top:312px">school</span>
      <span class="word word--md" style="left:215px;top:321px">education</span>
      <span class="word" style="left:17px;top:344px">educator</span>
      <span class="word" style="left:267px;top:369px">society</span>
      <span class="word word--md" style="left:111px;top:390px">text</span>
      <span class="word" style="left:26px;top:406px">guardian</span>
      <span class="word" style="left:174px;top:398px">activity</span>
      <span class="word word--md" style="left:244px;top:410px">platform</span>
      <span class="word" style="left:66px;top:442px">online</span>
      <span class="word" style="left:150px;top:438px">collaboration</span>
      <span class="word word--md" style="left:180px;top:471px">social</span>
      <span class="word" style="left:32px;top:482px">media</span>
      <span class="word" style="left:259px;top:493px">pupil</span>
      <span class="word" style="left:90px;top:506px">guiding</span>
      <span class="word word--md" style="left:175px;top:510px">learning</span>
      <span class="word" style="left:35px;top:524px">guru</span>
      <span class="word" style="left:275px;top:546px">voice</span>
      <span class="word word--lg" style="left:22px;top:563px">collaborative</span>
      <span class="word" style="left:224px;top:572px">friendly</span>
    </div>
    <div class="brand-mark" style="top:242px;width:80px;height:80px;"></div>
    <div class="brand-name" style="top:362px;font-size:17px;letter-spacing:9px;">MORLAVIK</div>
  </section>

  <!-- Concept 3 -->
  <h2 class="concept-label" style="left:282px; top:766px;">#3</h2>
  <section class="screen screen--teal" style="left:282px; top:805px;">
    <div class="screen-photo" role="img" aria-label="Teal-tinted photo of students studying with open books at a desk"></div>
    <div class="status-bar">
      <svg class="signal" width="50" height="10" viewBox="0 0 50 10"><g fill="#fff"><circle cx="3" cy="5" r="2.5"/><circle cx="9" cy="5" r="2.5"/><circle cx="15" cy="5" r="2.5"/></g><g fill="none" stroke="#fff"><circle cx="21" cy="5" r="2"/><circle cx="27" cy="5" r="2"/></g><path d="M36 7 l3 3 3-3 M34 4.5 a7 7 0 0 1 10 0" fill="none" stroke="#fff" stroke-width="1.4"/></svg>
      <div class="clock">4:21 PM</div>
      <div class="battery">100% <svg width="24" height="10" viewBox="0 0 24 10"><rect x="0" y="0" width="22" height="10" rx="2" fill="#fff"/><rect x="22" y="3" width="2" height="4" fill="#fff"/></svg></div>
    </div>
    <div class="word-cloud">
      <span class="word" style="left:17px;top:55px">learner</span>
      <span class="word word--md" style="left:150px;top:52px;opacity:.35">guidance</span>
      <span class="word" style="left:256px;top:70px">secure</span>
      <span class="word word--md" style="left:56px;top:92px;opacity:.4">student</span>
      <span class="word word--lg" style="left:183px;top:85px;opacity:.4">safe</span>
      <span class="word" style="left:138px;top:108px">parent</span>
      <span class="word" style="left:257px;top:100px">tutor</span>
      <span class="word" style="left:50px;top:125px">teacher</span>
      <span class="word" style="left:213px;top:134px">texting</span>
      <span class="word" style="left:5px;top:157px">community</span>
      <span class="word" style="left:247px;top:169px">teaching</span>
      <span class="word word--lg" style="left:14px;top:186px;opacity:.4">chat</span>
      <span class="word" style="left:54px;top:211px">school</span>
      <span class="word word--md" style="left:219px;top:220px;opacity:.35">education</span>
      <span class="word" style="left:12px;top:243px">educator</span>
      <span class="word word--md" style="left:91px;top:271px;opacity:.3">text</span>
      <span class="word" style="left:237px;top:264px">society</span>
      <span class="word" style="left:0px;top:321px">guardian</span>
      <span class="word word--md" style="left:250px;top:326px;opacity:.35">platform</span>
      <span class="word" style="left:61px;top:341px">online</span>
      <span class="word" style="left:136px;top:337px">collaboration</span>
      <span class="word" style="left:100px;top:370px">activity</span>
      <span class="word word--md" style="left:181px;top:374px;opacity:.35">social</span>
      <span class="word" style="left:27px;top:381px">media</span>
      <span class="word" style="left:254px;top:393px">pupil</span>
      <span class="word" style="left:104px;top:401px">curriculum</span>
    </div>
    <div class="brand-mark" style="top:140px;width:96px;height:96px;"></div>
    <div class="brand-name" style="top:301px;font-size:22px;letter-spacing:13px;">MORLAVIK</div>
    <p class="tagline">Communicate with other students, teachers,<br>and parents through secure and safe platform</p>
    <div class="cta">GET STARTED NOW <svg width="24" height="14" viewBox="0 0 24 14"><path d="M1 7h21M16 1l6 6-6 6" fill="none" stroke="#3cc0c4" stroke-width="1.8"/></svg></div>
  </section>

  <!-- Concept 4 -->
  <h2 class="concept-label" style="left:667px; top:766px;">#4</h2>
  <section class="screen screen--teal" style="left:667px; top:805px;">
    <div class="screen-photo" role="img" aria-label="Teal-tinted photo of students studying with open books at a desk"></div>
    <div class="status-bar">
      <svg class="signal" width="50" height="10" viewBox="0 0 50 10"><g fill="#fff"><circle cx="3" cy="5" r="2.5"/><circle cx="9" cy="5" r="2.5"/><circle cx="15" cy="5" r="2.5"/></g><g fill="none" stroke="#fff"><circle cx="21" cy="5" r="2"/><circle cx="27" cy="5" r="2"/></g><path d="M36 7 l3 3 3-3 M34 4.5 a7 7 0 0 1 10 0" fill="none" stroke="#fff" stroke-width="1.4"/></svg>
      <div class="clock">4:21 PM</div>
      <div class="battery">100% <svg width="24" height="10" viewBox="0 0 24 10"><rect x="0" y="0" width="22" height="10" rx="2" fill="#fff"/><rect x="22" y="3" width="2" height="4" fill="#fff"/></svg></div>
    </div>
    <div class="word-cloud">
      <span class="word" style="left:43px;top:55px">learner</span>
      <span class="word word--bright" style="left:144px;top:49px;font-size:16px">media</span>
      <span class="word" style="left:256px;top:70px">secure</span>
      <span class="word word--md word--bright" style="left:33px;top:94px">student</span>
      <span class="word word--lg word--bright" style="left:183px;top:85px">safe</span>
      <span class="word" style="left:138px;top:108px">parent</span>
      <span class="word" style="left:257px;top:100px">tutor</span>
      <span class="word" style="left:50px;top:125px">teacher</span>
      <span class="word" style="left:213px;top:134px">texting</span>
      <span class="word" style="left:5px;top:157px">community</span>
      <span class="word word--bright" style="left:247px;top:169px;font-size:16px">teaching</span>
      <span class="word word--lg word--bright" style="left:14px;top:186px">chat</span>
      <span class="word" style="left:54px;top:211px">school</span>
      <span class="word word--md" style="left:219px;top:220px;opacity:.35">education</span>
      <span class="word" style="left:12px;top:243px">educator</span>
      <span class="word word--md" style="left:91px;top:271px;opacity:.3">text</span>
      <span class="word" style="left:237px;top:264px">society</span>
      <span class="word" style="left:0px;top:321px">guardian</span>
      <span class="word word--md word--bright" style="left:250px;top:326px">platform</span>
      <span class="word" style="left:61px;top:341px">online</span>
      <span class="word" style="left:136px;top:337px;opacity:.45">collaboration</span>
      <span class="word" style="left:100px;top:370px">activity</span>
      <span class="word word--md word--bright" style="left:181px;top:374px">social</span>
      <span class="word word--md word--bright" style="left:8px;top:389px">guidance</span>
      <span class="word" style="left:254px;top:393px">pupil</span>
      <span class="word" style="left:114px;top:408px">curriculum</span>
    </div>
    <div class="brand-mark" style="top:140px;width:96px;height:96px;"></div>
    <div class="brand-name" style="top:301px;font-size:22px;letter-spacing:13px;">MORLAVIK</div>
    <p class="tagline">Communicate with other students, teachers,<br>and parents through secure and safe platform</p>
    <div class="cta">GET STARTED NOW <svg width="24" height="14" viewBox="0 0 24 14"><path d="M1 7h21M16 1l6 6-6 6" fill="none" stroke="#3cc0c4" stroke-width="1.8"/></svg></div>
  </section>

</main>
</body>
</html>
```